Rig up a website for a Rigging Company

We already have a logo. Looking for a website design that works on pavlune.com.
Our rigging company uses semi trucks, forklifts, and similar equipment to move large machines.
Our logo is white, black and red.

Target Market(s)

Medical Industry (moving medical equipment), Utility Industry (power equipment), Food Industry (moving bottling/packing equipment), US Government (large equipment)

Industry/Entity Type

It Company

Coding

Coded - Design and coding required

Number of Pages Required

5+ page

Font styles to use
Sans Serif

Colors
ec1f27
ffffff
0355a3

Requirements
Must have
• Home page, About page, Services Page, and Contact Information page
Nice to have
• Pictures of semi and forklifts and ability to insert our own pictures of our equipment

```html
<!DOCTYPE html>
<html lang="en">
<head>
<meta charset="utf-8">
<title>Hollis Rigging</title>
<link rel="stylesheet" href="https://fonts.googleapis.com/css2?family=Roboto+Condensed:wght@400;700&family=Open+Sans:ital,wght@0,400;0,600;1,400&display=swap">
<style>
:root{
  --red:#e3151c;
  --ink:#222222;
  --text:#555555;
  --muted:#8a8a8a;
  --white:#ffffff;
  --dark:#2b2b2b;
  --footer:#1b1b1b;
  --bar:#0f0f0f;
  --line:#e5e5e5;
}
*{box-sizing:border-box;margin:0;padding:0}
html,body{width:1200px;height:2719px;overflow:hidden;background:var(--white)}
body{position:relative;font-family:"Open Sans",Arial,sans-serif;color:var(--text)}
.abs{position:absolute}
.head-font{font-family:"Roboto Condensed","Arial Narrow",sans-serif}

/* header */
.site-header{top:0;left:0;width:1200px;height:120px;background:var(--white)}
.brand{left:100px;top:32px;display:flex;align-items:center;gap:10px}
.brand-mark{width:22px;height:22px;background:var(--red)}
.brand-name{font-family:"Roboto Condensed",sans-serif;font-weight:700;font-size:34px;color:var(--ink);letter-spacing:1px}
.top-contact{top:24px;right:100px;display:flex;gap:34px;font-size:14px;color:var(--text)}
.top-contact span{display:flex;align-items:center;gap:12px}
.dot-icon{width:26px;height:26px;border-radius:50%;background:var(--red);display:flex;align-items:center;justify-content:center}
.main-nav{top:80px;right:100px;display:flex;gap:32px;font-size:13px;color:var(--ink);text-transform:uppercase}
.main-nav .active{color:var(--red)}

/* hero */
.hero{top:120px;left:0;width:1200px;height:532px;background:linear-gradient(90deg,#3a3f48 0%,#55606d 40%,#6b5a40 75%,#3b3225 100%)}
.hero-title{left:98px;top:210px;font-size:50px;font-weight:700;color:var(--white);letter-spacing:1px}
.hero-sub{left:98px;top:276px;width:420px;font-size:14px;font-weight:600;color:var(--white);line-height:21px}
.hero-dots{left:98px;top:334px;display:flex;gap:8px}
.hero-dots i{width:12px;height:12px;border-radius:50%;background:var(--white);display:block}
.hero-dots i.on{box-shadow:0 0 0 3px rgba(255,255,255,.5)}

/* services */
.service{top:596px;width:240px;text-align:center}
.service-icon{width:114px;height:114px;margin:0 auto;border-radius:50%;background:var(--red);border:5px solid var(--white);box-shadow:0 0 0 1px #ddd;display:flex;align-items:center;justify-content:center}
.service h3{margin-top:20px;font-family:"Roboto Condensed",sans-serif;font-weight:400;font-size:17px;color:var(--ink);text-transform:uppercase}
.service p{margin-top:12px;font-size:11.5px;line-height:20px;color:var(--text)}
.service .chev{margin-top:8px}

/* welcome */
.welcome-img{left:100px;top:935px;width:380px;height:305px;background:radial-gradient(ellipse at 60% 50%,#d7a86a 0%,#c79a5a 30%,#e8c34a 55%,#fff 75%)}
.welcome{left:530px;top:968px;width:560px}
.welcome h2{font-family:"Roboto Condensed",sans-serif;font-weight:700;font-size:30px;color:var(--ink)}
.welcome h2 em{font-style:normal;color:var(--red)}
.welcome p{margin-top:18px;font-size:11.5px;line-height:21px}
.btn-outline{display:inline-flex;align-items:center;gap:6px;margin-top:22px;padding:7px 10px;border:1px solid var(--red);color:var(--red);font-size:11px;font-weight:600;text-transform:uppercase;border-radius:2px}

/* recent work */
.work{top:1325px;left:0;width:1200px;height:550px;background:linear-gradient(180deg,#2e2e2e,#3a3530 60%,#2a2724)}
.work h2{position:absolute;top:60px;width:100%;text-align:center;font-family:"Roboto Condensed",sans-serif;font-weight:400;font-size:30px;color:var(--white)}
.work .rule{position:absolute;left:566px;top:115px;width:68px;height:8px;border-top:2px solid var(--white);border-bottom:2px solid var(--white)}
.card{top:169px;width:232px;height:286px;background:var(--white)}
.card-img{height:186px}
.card h4{margin-top:18px;text-align:center;font-weight:400;font-size:15px;color:var(--red)}
.card p{margin:8px 18px 0;text-align:center;font-size:11.5px;line-height:19px}

/* testimonials */
.avatar{left:528px;top:1943px;width:144px;height:144px;border-radius:50%;border:5px solid #eaeaea;background:linear-gradient(180deg,#8fb8d8,#3c6b94)}
.testi-title{top:2112px;width:1200px;text-align:center;font-family:"Roboto Condensed",sans-serif;font-size:28px;color:var(--ink)}
.testi-quote{left:180px;top:2165px;width:840px;text-align:center;font-style:italic;font-size:12px;line-height:26px;color:var(--text)}
.testi-name{top:2258px;width:1200px;text-align:center;font-size:15px}
.testi-name b{color:var(--red);font-weight:600}
.arrow{top:2180px}

/* footer */
.site-footer{top:2363px;left:0;width:1200px;height:298px;background:var(--footer);color:#ddd}
.f-brand{left:100px;top:95px;font-family:"Roboto Condensed",sans-serif;font-weight:700;font-size:30px;color:var(--white);letter-spacing:1px}
.socials{left:100px;top:177px;display:flex;gap:7px}
.socials i{width:22px;height:22px;border-radius:50%;border:1px solid #bbb;display:block}
.f-col h5{font-family:"Roboto Condensed",sans-serif;font-weight:400;font-size:19px;color:var(--white);text-transform:uppercase}
.f-contact{left:340px;top:56px}
.f-row{display:flex;gap:16px;margin-top:18px;font-size:12.5px;line-height:20px;color:var(--white)}
.f-row svg{flex:none;margin-top:2px}
.f-links{left:657px;top:52px}
.f-links ul{list-style:none;margin-top:16px}
.f-links li{font-size:12px;line-height:24px;color:var(--white)}
.f-links li::before{content:"";display:inline-block;border-left:5px solid var(--white);border-top:4px solid transparent;border-bottom:4px solid transparent;margin-right:8px}
.f-news{left:857px;top:52px;width:242px}
.f-news p{margin-top:18px;font-size:11.5px;line-height:20px;color:var(--white)}
.f-input{margin-top:12px;height:42px;background:var(--white);font-size:11px;color:#777;padding:13px 14px}
.f-btn{display:inline-block;margin-top:12px;padding:8px 14px;border:1px solid var(--white);font-size:12px;color:var(--white);text-transform:uppercase}
.copy-bar{top:2661px;left:0;width:1200px;height:58px;background:var(--bar);text-align:center;line-height:58px;font-size:12px;color:var(--white)}
</style>
</head>
<body>

<header class="site-header abs">
  <div class="brand abs"><span class="brand-mark"></span><span class="brand-name">HOLLIS RIGGING</span></div>
  <div class="top-contact abs">
    <span><i class="dot-icon"><svg width="12" height="12" viewBox="0 0 24 24"><path fill="#fff" d="M6.6 10.8a15 15 0 006.6 6.6l2.2-2.2c.3-.3.7-.4 1-.2 1.1.4 2.3.6 3.6.6.6 0 1 .4 1 1V20c0 .6-.4 1-1 1A17 17 0 013 4c0-.6.4-1 1-1h3.5c.6 0 1 .4 1 1 0 1.3.2 2.5.6 3.6.1.3 0 .7-.2 1z"/></svg></i>(555) 204-7180</span>
    <span><i class="dot-icon"><svg width="12" height="12" viewBox="0 0 24 24"><path fill="#fff" d="M2 5h20v14H2z"/><path fill="none" stroke="#e3151c" stroke-width="2" d="M2 5l10 8 10-8"/></svg></i>info@hollisrigging.com</span>
  </div>
  <nav class="main-nav abs">
    <span class="active">Home</span><span>About Us</span><span>Services</span><span>Projects</span><span>Blog</span><span>Contact Us</span>
  </nav>
</header>

<section class="hero abs" role="img" aria-label="Warehouse interior with a heavy crane hook hanging from cables">
  <h1 class="hero-title abs head-font" style="top:210px">HOLLIS RIGGING</h1>
  <p class="hero-sub abs">Sed ut perspiciatis unde omnis iste natus sit voluptatem accusantium doloremque laudantium, totam</p>
  <div class="hero-dots abs"><i class="on"></i><i></i><i></i><i></i></div>
</section>

<section class="services">
  <div class="service abs" style="left:88px">
    <div class="service-icon"><svg width="50" height="50" viewBox="0 0 50 50" fill="none" stroke="#fff" stroke-width="2.5"><path d="M8 44h30M14 44V14l26-8M14 14h14M36 7v16M32 23h8v5h-8zM18 44v-8h12v8"/></svg></div>
    <h3>Machinery Moving</h3>
    <p>Sed ut perspiciatis unde omnis iste natus error sit voluptatem accusantium doque laudantium, totam rem dolores</p>
    <svg class="chev" width="14" height="14" viewBox="0 0 14 14" fill="none" stroke="#555" stroke-width="1.5"><path d="M3 3l4 4 4-4M3 8l4 4 4-4"/></svg>
  </div>
  <div class="service abs" style="left:353px">
    <div class="service-icon"><svg width="50" height="50" viewBox="0 0 50 50" fill="none" stroke="#fff" stroke-width="2.5"><path d="M14 8h22v18H14zM12 26h26v12H12zM18 14h14M16 44v-6M34 44v-6"/></svg></div>
    <h3>Semi Trucks</h3>
    <p>Sed ut perspiciatis unde omnis iste natus error sit voluptatem accusantium doque laudantium, totam rem dolores</p>
    <svg class="chev" width="14" height="14" viewBox="0 0 14 14" fill="none" stroke="#555" stroke-width="1.5"><path d="M3 3l4 4 4-4M3 8l4 4 4-4"/></svg>
  </div>
  <div class="service abs" style="left:618px">
    <div class="service-icon"><svg width="50" height="50" viewBox="0 0 50 50" fill="none" stroke="#fff" stroke-width="2.5"><path d="M8 34V18h14l6 10v6zM14 18v-8h8M32 10v28h12"/><circle cx="14" cy="38" r="4"/><circle cx="26" cy="38" r="4"/></svg></div>
    <h3>Forklifts</h3>
    <p>Sed ut perspiciatis unde omnis iste natus error sit voluptatem accusantium doque laudantium, totam rem dolores</p>
    <svg class="chev" width="14" height="14" viewBox="0 0 14 14" fill="none" stroke="#555" stroke-width="1.5"><path d="M3 3l4 4 4-4M3 8l4 4 4-4"/></svg>
  </div>
  <div class="service abs" style="left:875px">
    <div class="service-icon"><svg width="50" height="50" viewBox="0 0 50 50" fill="none" stroke="#fff" stroke-width="2.5"><path d="M25 6v8M20 14h10v6H20zM25 20v10a7 7 0 11-7 7"/></svg></div>
    <h3>Similar Equipment</h3>
    <p>Sed ut perspiciatis unde omnis iste natus error sit voluptatem accusantium doque laudantium, totam rem dolores</p>
    <svg class="chev" width="14" height="14" viewBox="0 0 14 14" fill="none" stroke="#555" stroke-width="1.5"><path d="M3 3l4 4 4-4M3 8l4 4 4-4"/></svg>
  </div>
</section>

<section>
  <div class="welcome-img abs" role="img" aria-label="Yellow forklift carrying stacked cardboard boxes on a pallet"></div>
  <div class="welcome abs">
    <h2>WELCOME TO <em>HOLLIS RIGGING</em></h2>
    <p>Nemo enim ipsam voluptatem quia voluptas sit aspernatur aut odit aut fugit, sed quia consequuntur magni dolores eos qui ratione voluptatem sequi nesciunt. Neque porro quisquam est, qui dolorem ipsum quia dolor sit amet, consectetur, adipisci velit, sed quia non numquam eius modi tempora incidunt ut labore et dolore magnam aliquam quaerat</p>
    <p style="margin-top:12px">Nemo enim ipsam voluptatem quia voluptas sit aspernatur aut odit aut fugit, sed quia consequuntur magni dolores eos qui ratione voluptatem sequi nesciunt. Neque porro quisquam est, qui dolorem ipsum quia dolor sit amet, consectetur, adipisci velit.</p>
    <span class="btn-outline">Read More <svg width="10" height="10" viewBox="0 0 10 10"><circle cx="5" cy="5" r="5" fill="#e3151c"/><path d="M4 3l2 2-2 2" stroke="#fff" fill="none"/></svg></span>
  </div>
</section>

<section class="work abs">
  <h2>RECENT WORK</h2>
  <div class="rule"></div>
  <article class="card abs" style="left:98px"><div class="card-img" role="img" aria-label="Forklift loading goods at a warehouse dock" style="background:linear-gradient(135deg,#e0a050,#b0542a 50%,#5a4a3c)"></div><h4>Sed ut perspiciatis unde</h4><p>Sed ut perspiciatis unde omnis iste natus error sit voluptatem</p></article>
  <article class="card abs" style="left:354px"><div class="card-img" role="img" aria-label="Semi truck hauling an orange shipping container" style="background:linear-gradient(180deg,#8ab8e0,#cfd9e2 45%,#b0603a 60%,#7a7a7a)"></div><h4>Sed ut perspiciatis unde</h4><p>Sed ut perspiciatis unde omnis iste natus error sit voluptatem</p></article>
  <article class="card abs" style="left:611px"><div class="card-img" role="img" aria-label="Container handler lifting a shipping container at a port" style="background:linear-gradient(135deg,#a89890,#c05030 55%,#5c6e80)"></div><h4>Sed ut perspiciatis unde</h4><p>Sed ut perspiciatis unde omnis iste natus error sit voluptatem</p></article>
  <article class="card abs" style="left:868px"><div class="card-img" role="img" aria-label="Yellow crane at an industrial site" style="background:linear-gradient(135deg,#7a8a9a,#c8b040 50%,#505860)"></div><h4>Sed ut perspiciatis unde</h4><p>Sed ut perspiciatis unde omnis iste natus error sit voluptatem</p></article>
</section>

<section>
  <div class="avatar abs" role="img" aria-label="Customer portrait in a hard hat"></div>
  <h2 class="testi-title abs">CUSTOMER TESTIMONIALS</h2>
  <p class="testi-quote abs">“ Lorem ipsum dolor sit amet, consectetur adipiscing elit, sed do eiusmod tempor incididunt ut labore et dolore magna aliqua. Ut enim ad minim veniam, quis nostrud exercitation ullamco laboris nisi ut aliquip ex ea commodo consequat. Duis aute irure dolor in reprehenderit in voluptate velit esse cillum dolore eu fugiat nulla pariatur. Excepteur sint occaecat ”</p>
  <p class="testi-name abs"><b>Sam Porter</b> - Hollis Rigging</p>
  <svg class="arrow abs" style="left:96px" width="20" height="40" viewBox="0 0 20 40" fill="none" stroke="#bbb" stroke-width="1.5"><path d="M18 2L2 20l16 18"/></svg>
  <svg class="arrow abs" style="left:1084px" width="20" height="40" viewBox="0 0 20 40" fill="none" stroke="#bbb" stroke-width="1.5"><path d="M2 2l16 18L2 38"/></svg>
</section>

<footer class="site-footer abs">
  <div class="f-brand abs">HOLLIS RIGGING</div>
  <div class="socials abs"><i></i><i></i><i></i><i></i><i></i></div>
  <div class="f-col f-contact abs">
    <h5>Contact Us</h5>
    <div class="f-row"><svg width="16" height="18" viewBox="0 0 16 18" fill="none" stroke="#fff" stroke-width="1.5"><path d="M8 17s6-6 6-10A6 6 0 002 7c0 4 6 10 6 10z"/><circle cx="8" cy="7" r="2"/></svg><span>Hollis Rigging<br>412 E. Harbor Road, Suite 210</span></div>
    <div class="f-row"><svg width="16" height="16" viewBox="0 0 24 24" fill="none" stroke="#fff" stroke-width="1.8"><path d="M6.6 10.8a15 15 0 006.6 6.6l2.2-2.2 5 1.6V21A17 17 0 013 4h4.2l1.6 5z"/></svg><span>Phone : +(555) 3812 0946</span></div>
    <div class="f-row"><svg width="16" height="14" viewBox="0 0 16 14" fill="none" stroke="#fff" stroke-width="1.5"><path d="M1 2h14v10H1zM1 2l7 6 7-6"/></svg><span>info@hollisrigging.com</span></div>
  </div>
  <div class="f-col f-links abs">
    <h5>Quick Links</h5>
    <ul><li>Home</li><li>About Us</li><li>Services</li><li>Photo Gallery</li><li>Projects</li><li>Contact Us</li></ul>
  </div>
  <div class="f-col f-news abs">
    <h5>Join Our Newsletter</h5>
    <p>Sed ut perspiciatis unde omnis iste natus error sit voluptatem accusantium dolore</p>
    <div class="f-input">Enter Email</div>
    <span class="f-btn">Subscribe</span>
  </div>
</footer>
<div class="copy-bar abs">Copyright © Hollis Rigging 2017. All rights reserved.</div>

</body>
</html>
```